Corvane Freight Company Business Card Design

We are a company that delivers natural saltwater (from the ocean) to aquarium companies, restaurants and home marine tanks. I would like a new business card to suit.

Must include Name, company name, abn, contact number and website as well as logo (see attached).

Looking for a design that stands out, has a clean but unique appearance.

Double and single sided entries welcome

Business

• Logo

```html
<!DOCTYPE html>
<html lang="en">
<head>
<meta charset="utf-8">
<title>Corvane Freight Company – Business Card</title>
<link href="https://fonts.googleapis.com/css2?family=Open+Sans:wght@400;700&display=swap" rel="stylesheet">
<style>
  :root {
    --backdrop: #161616;
    --card-white: #ffffff;
    --card-edge: #bdbdbd;
    --brand-blue: #0a5bab;
    --sky-blue: #55cbf3;
    --logo-blue: #0b8fd0;
    --band-ink: #1462b2;
    --body-ink: #1e1e1e;
  }
  * { box-sizing: border-box; margin: 0; padding: 0; }
  html, body { width: 1200px; height: 750px; overflow: hidden; }
  body {
    background: var(--backdrop);
    font-family: "Open Sans", sans-serif;
    position: relative;
  }
  .card {
    position: absolute;
    width: 515px;
    height: 293px;
    border-radius: 22px;
    background: var(--card-white);
    border: 1px solid var(--card-edge);
    overflow: hidden;
  }
  .card--front-light { left: 73px; top: 62px; }
  .card--front-dark  { left: 608px; top: 62px; }
  .card--back {
    left: 340px; top: 416px;
    background: var(--brand-blue);
    border-color: #d8d8d8;
    display: flex; align-items: center; justify-content: center;
  }
  .wordmark {
    position: absolute;
    left: 28px; top: 122px;
    font-size: 31px;
    font-weight: 700;
    color: var(--logo-blue);
    letter-spacing: -0.5px;
    white-space: nowrap;
  }
  .wordmark--large {
    position: static;
    font-size: 54px;
    color: var(--card-white);
  }
  .name-band {
    position: absolute;
    left: 297px; top: 62px;
    width: 218px; height: 46px;
    padding: 1px 0 0 13px;
    line-height: 1.2;
  }
  .card--front-light .name-band { background: var(--sky-blue); color: var(--band-ink); }
  .card--front-dark  .name-band { background: var(--brand-blue); color: var(--card-white); }
  .name-band .person { font-size: 18px; font-weight: 700; display: block; }
  .name-band .role { font-size: 14px; display: block; }
  .contact {
    position: absolute;
    left: 297px; top: 128px;
    font-size: 12.6px;
    color: var(--body-ink);
    line-height: 20px;
  }
  .contact .row { display: flex; align-items: center; gap: 6px; }
  .contact .row svg { width: 10px; height: 10px; flex: none; }
  .contact .address { margin-top: 10px; line-height: 19px; }
  .contact .abn { margin-top: 2px; }
</style>
</head>
<body>

  <section class="card card--front-light" aria-label="Card front, light blue variant">
    <div class="wordmark">Corvane Freight</div>
    <div class="name-band"><span class="person">Your Name</span><span class="role">Title</span></div>
    <div class="contact">
      <div class="row">
        <svg viewBox="0 0 10 10" aria-hidden="true"><circle cx="5" cy="5" r="4.6" fill="none" stroke="#1e1e1e" stroke-width="1"/><path d="M3.3 2.6 L4.3 3.6 L3.8 4.3 Q4.6 5.7 5.8 6.2 L6.5 5.6 L7.4 6.6 L6.6 7.4 Q3.2 6.6 2.6 3.3 Z" fill="#1e1e1e"/></svg>
        <span>123-456-7892</span>
      </div>
      <div class="row">
        <svg viewBox="0 0 10 10" aria-hidden="true"><circle cx="5" cy="5" r="4.3" fill="none" stroke="#1e1e1e" stroke-width="1"/><ellipse cx="5" cy="5" rx="1.8" ry="4.3" fill="none" stroke="#1e1e1e" stroke-width="0.8"/><line x1="0.7" y1="5" x2="9.3" y2="5" stroke="#1e1e1e" stroke-width="0.8"/></svg>
        <span>www.corvanefreight.com</span>
      </div>
      <div class="address">Street Name, City Name ,<br>State, Zip Code</div>
      <div class="abn">ABN: 123456789</div>
    </div>
  </section>

  <section class="card card--front-dark" aria-label="Card front, dark blue variant">
    <div class="wordmark">Corvane Freight</div>
    <div class="name-band"><span class="person">Your Name</span><span class="role">Title</span></div>
    <div class="contact">
      <div class="row">
        <svg viewBox="0 0 10 10" aria-hidden="true"><circle cx="5" cy="5" r="4.6" fill="none" stroke="#1e1e1e" stroke-width="1"/><path d="M3.3 2.6 L4.3 3.6 L3.8 4.3 Q4.6 5.7 5.8 6.2 L6.5 5.6 L7.4 6.6 L6.6 7.4 Q3.2 6.6 2.6 3.3 Z" fill="#1e1e1e"/></svg>
        <span>123-456-7892</span>
      </div>
      <div class="row">
        <svg viewBox="0 0 10 10" aria-hidden="true"><circle cx="5" cy="5" r="4.3" fill="none" stroke="#1e1e1e" stroke-width="1"/><ellipse cx="5" cy="5" rx="1.8" ry="4.3" fill="none" stroke="#1e1e1e" stroke-width="0.8"/><line x1="0.7" y1="5" x2="9.3" y2="5" stroke="#1e1e1e" stroke-width="0.8"/></svg>
        <span>www.corvanefreight.com</span>
      </div>
      <div class="address">Street Name, City Name ,<br>State, Zip Code</div>
      <div class="abn">ABN: 123456789</div>
    </div>
  </section>

  <section class="card card--back" aria-label="Card back">
    <div class="wordmark wordmark--large">Corvane Freight</div>
  </section>

</body>
</html>
```